Veldmark Supplies Business Card

Professional business card that stand out to our potential customers. Front and back with clean modern design

Industry/Entity Type

Oil and gas

Contact Information for Business Card

Name, address, website , office phone and cell number

Requirements
Must have
• Editable files for each employee

```html
<!DOCTYPE html>
<html lang="en">
<head>
<meta charset="utf-8">
<title>Veldmark Supplies Business Card</title>
<link rel="stylesheet" href="https://fonts.googleapis.com/css2?family=Montserrat:wght@400;500;800&display=swap">
<style>
  :root {
    --cyan: #0bafd3;
    --red: #e3232a;
    --ink: #1d1d1f;
    --paper: #ffffff;
    --backdrop: #3b3c3e;
  }
  html, body {
    margin: 0;
    width: 1200px;
    height: 1200px;
    overflow: hidden;
    background: var(--backdrop);
    font-family: "Montserrat", sans-serif;
  }
  .sheet {
    width: 1200px;
    height: 1200px;
    display: flex;
    flex-direction: column;
    align-items: center;
    justify-content: center;
    gap: 60px;
  }
  .card {
    position: relative;
    width: 900px;
    height: 514px;
    border-radius: 30px;
    overflow: hidden;
    box-shadow: 0 10px 30px rgba(0,0,0,.45);
  }
  /* front */
  .card-front { background: var(--cyan); }
  .front-brand {
    position: absolute;
    right: 70px;
    bottom: 90px;
    display: flex;
    align-items: center;
    gap: 16px;
    color: var(--paper);
    font-weight: 800;
    font-size: 44px;
    letter-spacing: 1px;
  }
  .brand-square { width: 30px; height: 30px; background: var(--paper); }
  /* back */
  .card-back { background: var(--paper); }
  .back-waves { position: absolute; inset: 0; }
  .back-brand {
    position: absolute;
    left: 0;
    right: 0;
    top: 70px;
    display: flex;
    justify-content: center;
    align-items: center;
    gap: 16px;
    color: var(--red);
    font-weight: 800;
    font-size: 46px;
    letter-spacing: 1px;
  }
  .back-brand .brand-square { background: var(--red); width: 32px; height: 32px; }
  .holder {
    position: absolute;
    left: 120px;
    top: 200px;
    width: 280px;
    text-align: right;
  }
  .holder-name { margin: 0; color: var(--red); font-weight: 800; font-size: 30px; }
  .holder-title { margin: 4px 0 0; color: var(--ink); font-weight: 400; font-size: 18px; }
  .divider {
    position: absolute;
    left: 420px;
    top: 174px;
    width: 2px;
    height: 130px;
    background: var(--red);
  }
  .contacts {
    position: absolute;
    left: 444px;
    top: 170px;
    margin: 0;
    padding: 0;
    list-style: none;
    font-size: 17px;
    color: var(--ink);
  }
  .contacts li { display: flex; align-items: center; gap: 10px; height: 33px; }
  .contacts svg { width: 18px; height: 18px; fill: var(--cyan); flex: none; }
  .address {
    position: absolute;
    left: 0;
    right: 0;
    top: 336px;
    text-align: center;
    font-size: 17px;
    color: var(--ink);
    margin: 0;
  }
</style>
</head>
<body>
<main class="sheet">
  <section class="card card-front" aria-label="Card front">
    <div class="front-brand"><span class="brand-square"></span>VELDMARK SUPPLIES</div>
  </section>

  <section class="card card-back" aria-label="Card back">
    <svg class="back-waves" viewBox="0 0 900 514" aria-hidden="true">
      <path d="M0 514 L0 475 C 300 455, 640 440, 900 330 L900 514 Z" fill="var(--cyan)"/>
      <path d="M420 470 C 650 445, 830 400, 900 310 L900 322 C 830 412, 650 455, 420 470 Z" fill="var(--paper)"/>
      <path d="M640 440 C 790 420, 880 360, 900 290 L900 298 C 880 370, 790 428, 640 440 Z" fill="var(--cyan)"/>
      <path d="M600 425 C 760 405, 870 340, 900 225 L900 252 C 870 360, 760 413, 600 425 Z" fill="var(--red)"/>
    </svg>

    <div class="back-brand"><span class="brand-square"></span>VELDMARK SUPPLIES</div>

    <div class="holder">
      <p class="holder-name">Tomas Verhoek</p>
      <p class="holder-title">President</p>
    </div>

    <div class="divider"></div>

    <ul class="contacts">
      <li><svg viewBox="0 0 24 24"><path d="M3 8c0-2 2-4 9-4s9 2 9 4v2h-5V8H8v2H3z M5 12h14l1 8H4z"/></svg>+1.555.010.0900 x123</li>
      <li><svg viewBox="0 0 24 24"><path d="M6 2l4 4-2 3c1 3 4 6 7 7l3-2 4 4-3 4C10 21 3 14 2 5z"/></svg>+1.555.012.3456</li>
      <li><svg viewBox="0 0 24 24"><path d="M2 5h20v2l-10 6L2 7z M2 9l10 6 10-6v10H2z"/></svg>info@veldmarksupplies.com</li>
      <li><svg viewBox="0 0 24 24"><circle cx="12" cy="12" r="10"/><path d="M2 12h20M12 2c4 4 4 16 0 20M12 2c-4 4-4 16 0 20" stroke="#fff" stroke-width="1.5" fill="none"/></svg>www.veldmarksupplies.com</li>
    </ul>

    <p class="address">48 Meridian Park Lane, Fairhollow, TX 79701 USA</p>
  </section>
</main>
</body>
</html>
```